RK Donnelly & Associates

Create a website encompassing design work already carried out for business card.
Small accounting practice, business accounting and management, superannuation, audit, taxation.

```html
<!DOCTYPE html>
<html lang="en">
<head>
<meta charset="utf-8">
<title>RK Donnelly &amp; Associates</title>
<link href="https://fonts.googleapis.com/css2?family=Oswald:wght@400;500&family=PT+Sans:wght@400;700&display=swap" rel="stylesheet">
<style>
:root{
  --bg:#1f1f21;
  --panel:#1a1a1b;
  --panel-edge:#2a2a2c;
  --nav:#222224;
  --text:#d6d6d6;
  --muted:#a9a9a9;
  --blue:#5b9bd5;
  --hero-top:#e9f3f8;
  --hero-bottom:#9fcbe0;
}
*{margin:0;padding:0;box-sizing:border-box}
html,body{width:1106px;height:1200px;overflow:hidden}
body{background:var(--bg);font-family:"PT Sans",sans-serif;color:var(--text);position:relative}
.abs{position:absolute}
.brand{left:158px;top:36px;display:flex;align-items:center;gap:10px}
.brand-mark{width:24px;height:24px;background:var(--blue)}
.brand-name{font-family:"PT Sans",sans-serif;font-weight:400;font-size:20px;line-height:24px;color:#fff}
.tollfree{left:686px;top:38px;font-size:20px;color:#e4e4e4;line-height:28px}
.tollfree .num{font-size:16px;letter-spacing:.5px}
.social{display:flex;gap:7px}
.social span{width:25px;height:25px;border:1.5px solid #8a8a8a;border-radius:50%;display:block}
.social.top{left:861px;top:52px}
.nav{left:158px;top:118px;width:790px;height:49px;background:var(--nav);border:1px solid var(--panel-edge);display:flex}
.nav a{color:#e8e8e8;text-decoration:none;font-size:14px;display:flex;align-items:center;justify-content:center;border-right:1px solid #2c2c2e}
.nav a.active{background:var(--blue);color:#fff}
.hero{left:158px;top:190px;width:790px;height:381px;background:linear-gradient(110deg,var(--hero-top) 0%,#d3e8f2 45%,var(--hero-bottom) 100%)}
.hero-photo{left:440px;top:0;width:350px;height:381px;background:linear-gradient(120deg,rgba(255,255,255,0) 0%,rgba(60,90,120,.35) 55%,#1b2838 100%)}
.hero-title{left:42px;top:78px;font-family:"Oswald",sans-serif;font-weight:500;color:#3b3b3b;line-height:1}
.hero-title .l1{font-size:38px;display:block}
.hero-title .l2{font-size:54px;color:var(--blue);display:block;margin-top:4px}
.hero-title .l3{font-size:38px;display:block;margin-top:8px}
.dots{left:50px;top:269px;display:flex;gap:6px}
.dots i{width:10px;height:10px;border-radius:50%;background:#111;display:block}
.dots i.on{background:var(--blue);box-shadow:0 0 0 2px #fff}
h2{font-weight:400;font-size:18px;color:#e0e0e0}
h2 em{font-style:normal;color:var(--blue)}
.services-head{left:158px;top:598px}
.services-list{left:158px;top:632px;width:242px;height:141px;border:1px solid var(--panel-edge);list-style:none;padding:12px 0 0 15px}
.services-list li{font-size:12px;color:#bdbdbd;height:24.5px;display:flex;align-items:center;gap:12px}
.welcome-photo{left:430px;top:602px;width:152px;height:171px;background:linear-gradient(160deg,#cfe0ea 0%,#7d97ab 50%,#2d3440 100%)}
.welcome{left:606px;top:598px;width:343px}
.welcome h2{padding-bottom:12px;border-bottom:1px solid #333}
.welcome p{font-size:9.6px;line-height:19px;color:#bdbdbd;margin-top:10px;text-align:justify}
.card{top:808px;width:241px;height:280px;background:var(--panel);border:1px solid #242426;padding:12px 14px}
.card h2{font-size:19px;height:30px;line-height:24px}
.card .pic{width:212px;height:111px;margin-top:8px}
.card p{font-size:9.6px;line-height:19px;color:#b5b5b5;margin-top:10px;text-align:justify}
.card .more{position:absolute;right:20px;bottom:12px;font-size:9.6px;color:var(--blue)}
.rule{left:158px;top:1123px;width:790px;height:1px;background:#2f2f31}
.copy{left:158px;top:1154px;font-size:9.6px;color:#a0a0a0}
.social.bottom{left:529px;top:1148px;gap:5px}
.social.bottom span{width:26px;height:26px}
.legal{left:793px;top:1154px;font-size:9.6px;color:#a0a0a0}
</style>
</head>
<body>
<header>
  <div class="abs brand"><span class="brand-mark"></span><span class="brand-name">RK Donnelly &amp; Associates</span></div>
  <div class="abs tollfree">Call us toll free :<br><span class="num">1 - 800 - 555 - 0142</span></div>
  <div class="abs social top" aria-label="Social links"><span></span><span></span><span></span></div>
  <nav class="abs nav">
    <a class="active" href="#" style="width:83px">Home</a>
    <a href="#" style="width:105px">About Us</a>
    <a href="#" style="width:120px">Our Services</a>
    <a href="#" style="width:96px">Practice</a>
    <a href="#" style="width:124px">Management</a>
    <a href="#" style="width:90px">Careers</a>
    <a href="#" style="width:109px;border-right:0">Contact Us</a>
  </nav>
</header>

<section class="abs hero">
  <div class="abs hero-photo" role="img" aria-label="Hand signing a document with a pen on a reflective desk"></div>
  <h1 class="abs hero-title"><span class="l1">BUSINESS</span><span class="l2">ACCOUNTING</span><span class="l3">AND MANAGEMENT</span></h1>
  <div class="abs dots"><i class="on"></i><i></i><i></i><i></i></div>
</section>

<h2 class="abs services-head">Our Services</h2>
<ul class="abs services-list">
  <li><svg width="11" height="11" viewBox="0 0 12 12"><circle cx="6" cy="6" r="6" fill="#fff"/><path d="M3.2 6.2l2 2 3.8-4" stroke="#1f1f21" stroke-width="1.6" fill="none"/></svg>Small Accounting Practice</li>
  <li><svg width="11" height="11" viewBox="0 0 12 12"><circle cx="6" cy="6" r="6" fill="#fff"/><path d="M3.2 6.2l2 2 3.8-4" stroke="#1f1f21" stroke-width="1.6" fill="none"/></svg>Business Accounting and Management</li>
  <li><svg width="11" height="11" viewBox="0 0 12 12"><circle cx="6" cy="6" r="6" fill="#fff"/><path d="M3.2 6.2l2 2 3.8-4" stroke="#1f1f21" stroke-width="1.6" fill="none"/></svg>Superannuation</li>
  <li><svg width="11" height="11" viewBox="0 0 12 12"><circle cx="6" cy="6" r="6" fill="#fff"/><path d="M3.2 6.2l2 2 3.8-4" stroke="#1f1f21" stroke-width="1.6" fill="none"/></svg>Audit</li>
  <li><svg width="11" height="11" viewBox="0 0 12 12"><circle cx="6" cy="6" r="6" fill="#fff"/><path d="M3.2 6.2l2 2 3.8-4" stroke="#1f1f21" stroke-width="1.6" fill="none"/></svg>Taxation</li>
</ul>

<div class="abs welcome-photo" role="img" aria-label="Businessman in a suit standing in an office"></div>
<div class="abs welcome">
  <h2>Welcome To <em>RK Donnelly &amp; Associates</em></h2>
  <p>Lorem ipsum dolor sit amet, consectetur adipisc ng elit. Proin ultricies vestibulum velit, bibendum condimentum metus faucibus sed. Lorem ipsum dolor sit amet, consectetur adipisc ng elit. Proin ultricies vestibulum velit, bibendum condimentum metus faucibus sed. Lorem ipsum dolor sit amet, consectetur adipisc ng elit. Proin ultricies vestibulum velit, bibendum condimentum metus faucibus sed. Lorem ipsum dolor sit amet, consectetur adipisc ng elit. Proin ultricies vestibulum velit, bibendum condimentum metus</p>
</div>

<article class="abs card" style="left:158px">
  <h2>Accounting <em>Practice</em></h2>
  <div class="pic" role="img" aria-label="Team meeting around a table" style="background:linear-gradient(135deg,#dfe6ec,#8a98a6 60%,#3a4350)"></div>
  <p>Lorem ipsum dolor sit amet, consectetur adipisc ng elit. Proin ultricies vestibulum velit, bibendum condimentum metus faucibus sed. Lorem ipsum dolor sit</p>
  <span class="more">Read More +</span>
</article>
<article class="abs card" style="left:433px">
  <h2><em>Business</em>&nbsp; Accounting</h2>
  <div class="pic" role="img" aria-label="Hands reviewing charts and a tablet" style="background:linear-gradient(135deg,#3b4a5c,#c9dbe8 55%,#e8f1f7)"></div>
  <p>Lorem ipsum dolor sit amet, consectetur adipisc ng elit. Proin ultricies vestibulum velit, bibendum condimentum metus faucibus sed. Lorem ipsum dolor sit</p>
  <span class="more">Read More +</span>
</article>
<article class="abs card" style="left:704px">
  <h2><em>Superannuation</em></h2>
  <div class="pic" role="img" aria-label="Retired couple reading documents together" style="background:linear-gradient(135deg,#e6dccb,#b7a27f 55%,#7d8a4a)"></div>
  <p>Lorem ipsum dolor sit amet, consectetur adipisc ng elit. Proin ultricies vestibulum velit, bibendum condimentum metus faucibus sed. Lorem ipsum dolor sit</p>
  <span class="more">Read More +</span>
</article>

<footer>
  <div class="abs rule"></div>
  <div class="abs copy">©2013 - 2014&nbsp; RK Donnelly &amp; Associates, All Rights Reserved.</div>
  <div class="abs social bottom" aria-label="Social links"><span></span><span></span><span></span><span></span><span></span></div>
  <div class="abs legal">Privacy Notice &nbsp;&nbsp;|&nbsp;&nbsp; Conditions of Use</div>
</footer>
</body>
</html>
```